Healthcare and Professional IT Services Company need a redesigned business card

We are a IT Services company that targets small medical practices and professional business such as Attorneys, Accounts, Architects etc. We want to communicate a professional yet friendly image using recent logo redesign here on ArtHarbor. Like to see the colors blue and orange in the design. Must use the Tall Pine Computing as displayed in the new logo - then also want to incorporate the fish logo as well.

Target Market(s)

Small medical and professional services

Industry/Entity Type

It Company

Contact Information for Business Card

The usual stuff, place for name address phone website. Also maybe our tagline which is "hooked on technology"

Requirements
Must have
• My new logo and the fish somewhere on the card

```html
<!DOCTYPE html>
<html lang="en">
<head>
<meta charset="utf-8">
<title>Tall Pine Computing – Business Card</title>
<link rel="stylesheet" href="https://fonts.googleapis.com/css2?family=Arimo:wght@400;700&display=swap">
<style>
  :root {
    --page-bg: #ecebe8;
    --card-white: #ffffff;
    --sky: #62c9f1;
    --sky-light: #8fd8f5;
    --band-blue: #4a74bf;
    --band-blue-deep: #4468b3;
    --ink-dark: #2b2b2b;
    --fish-orange: #f07a2a;
    --fish-teal: #3fb3c9;
    --text-white: #ffffff;
  }
  * { box-sizing: border-box; margin: 0; padding: 0; }
  html, body {
    width: 1200px; height: 892px; overflow: hidden;
    background: var(--page-bg);
    font-family: "Arimo", Arial, sans-serif;
  }
  .canvas { position: relative; width: 1200px; height: 892px; }

  .card {
    position: absolute;
    width: 620px; height: 354px;
    border-radius: 4px;
    overflow: hidden;
    box-shadow: 0 6px 18px rgba(0,0,0,.18);
  }

  /* Back of card */
  .card-back {
    left: 540px; top: 60px;
    background: linear-gradient(135deg, var(--sky) 0%, var(--sky-light) 100%);
  }
  .card-back .brand-name {
    position: absolute; left: 0; right: 0; top: 150px;
    text-align: center;
    font-weight: 700; font-size: 46px; letter-spacing: 1px;
    color: var(--text-white);
  }
  .faint-mark {
    position: absolute; width: 90px; height: 56px;
    border-radius: 50%;
    background: radial-gradient(ellipse, rgba(255,255,255,.35), rgba(255,255,255,0) 70%);
  }

  /* Front of card */
  .card-front {
    left: 40px; top: 478px;
    background: var(--card-white);
  }
  .logo-row {
    position: absolute; left: 36px; top: 52px;
    display: flex; align-items: center; gap: 18px;
  }
  .fish-illustration {
    width: 120px; height: 76px; border-radius: 50% 44% 44% 50%;
    background: linear-gradient(100deg, var(--fish-orange) 0%, var(--fish-teal) 60%, #7ccf6a 100%);
  }
  .card-front .brand-name {
    font-weight: 700; font-size: 40px; letter-spacing: .5px;
    color: var(--band-blue);
  }
  .stripe-light {
    position: absolute; left: 0; right: 0; top: 160px; height: 14px;
    background: var(--sky);
  }
  .contact-band {
    position: absolute; left: 0; right: 0; top: 174px; bottom: 0;
    background: linear-gradient(90deg, var(--band-blue-deep), var(--band-blue));
    display: flex; align-items: center; padding: 0 30px;
    color: var(--text-white);
  }
  .stripe-bottom {
    position: absolute; left: 0; right: 0; bottom: 0; height: 12px;
    background: var(--sky);
  }
  .person-name {
    font-weight: 700; font-size: 27px; width: 220px;
  }
  .divider {
    width: 2px; height: 110px; background: var(--text-white); margin: 0 18px 0 4px;
  }
  .contact-list { list-style: none; }
  .contact-list li {
    display: flex; align-items: center; gap: 10px;
    font-size: 16px; line-height: 27px;
  }
  .contact-list svg { width: 16px; height: 16px; flex: none; }
</style>
</head>
<body>
<div class="canvas">

  <section class="card card-back" aria-label="Card back">
    <div class="faint-mark" role="img" aria-label="Faint fish decoration" style="left:120px;top:40px"></div>
    <div class="faint-mark" role="img" aria-label="Faint fish decoration" style="left:500px;top:90px"></div>
    <div class="faint-mark" role="img" aria-label="Faint fish decoration" style="left:40px;top:230px"></div>
    <div class="faint-mark" role="img" aria-label="Faint fish decoration" style="left:430px;top:260px"></div>
    <div class="brand-name">Tall Pine Computing</div>
  </section>

  <section class="card card-front" aria-label="Card front">
    <div class="logo-row">
      <div class="fish-illustration" role="img" aria-label="Cartoon fish mascot illustration"></div>
      <div class="brand-name">Tall Pine Computing</div>
    </div>
    <div class="stripe-light"></div>
    <div class="contact-band">
      <div class="person-name">Marcus Ellery</div>
      <div class="divider"></div>
      <ul class="contact-list">
        <li>
          <svg viewBox="0 0 16 16"><rect x="0.5" y="0.5" width="15" height="15" rx="2" fill="#fff"/><path d="M4 4c1 0 1.5 2 1 2.6-.4.5.9 2.5 2.4 3.4.6-.5 2.6 0 2.6 1 0 .8-1 1.4-1.8 1.3C5.7 12 3.8 9 3.6 5.7 3.5 4.8 3.4 4 4 4z" fill="#4a74bf"/></svg>
          1300 555 014
        </li>
        <li>
          <svg viewBox="0 0 16 16"><rect x="0.5" y="0.5" width="15" height="15" rx="2" fill="#fff"/><rect x="3" y="5" width="10" height="7" fill="none" stroke="#4a74bf" stroke-width="1.2"/><path d="M3 5l5 4 5-4" fill="none" stroke="#4a74bf" stroke-width="1.2"/></svg>
          info@tallpinecomputing.com.au
        </li>
        <li>
          <svg viewBox="0 0 16 16"><rect x="0.5" y="0.5" width="15" height="15" rx="2" fill="#fff"/><circle cx="8" cy="8" r="4.5" fill="none" stroke="#4a74bf" stroke-width="1.2"/><path d="M3.5 8h9M8 3.5c-2 2.5-2 6.5 0 9M8 3.5c2 2.5 2 6.5 0 9" fill="none" stroke="#4a74bf" stroke-width="1"/></svg>
          www.tallpinecomputing.com
        </li>
        <li>
          <svg viewBox="0 0 16 16"><rect x="0.5" y="0.5" width="15" height="15" rx="2" fill="#fff"/><path d="M8 13s-3.5-4-3.5-6.3a3.5 3.5 0 0 1 7 0C11.5 9 8 13 8 13z" fill="#4a74bf"/><circle cx="8" cy="6.7" r="1.2" fill="#fff"/></svg>
          2210 W. Harbor Road Mesa, Arizona 85201
        </li>
      </ul>
    </div>
    <div class="stripe-bottom"></div>
  </section>

</div>
</body>
</html>
```